Business Card for Coastal Tundrabridge Advisory

We need a business card for Coastal Tundrabridge Advisory. The company website address is provided below. The company logo is attached. We provide specialized permafrost services to the mining, transportation, and oil & gas industries. The card should be prepared for:
Matthias Korhonen, PhD.
Coastal Tundrabridge Advisory
PO Box 418259
Quillwater, Alaska 99642
Direct: +1-907-555-0143
Email: mkorhonen@tundrabridgeadvisory.example
Website: www.coastaltundrabridgeadvisory.example

```html
<!DOCTYPE html>
<html lang="en">
<head>
<meta charset="utf-8">
<title>Coastal Tundrabridge Advisory – Business Card</title>
<link rel="stylesheet" href="https://fonts.googleapis.com/css2?family=Roboto:wght@300;400;500;700&display=swap">
<style>
  :root {
    --stage: #232323;
    --card: #111827;
    --ink: #ffffff;
    --ink-soft: #d9dee6;
    --ice: #4fb6e8;
    --ice-deep: #1f5f8f;
    --shade: #172233;
  }
  * { margin: 0; padding: 0; box-sizing: border-box; }
  html, body { width: 1200px; height: 711px; overflow: hidden; }
  body {
    background: var(--stage);
    font-family: "Roboto", Arial, sans-serif;
    color: var(--ink);
    position: relative;
  }
  .card {
    position: absolute;
    top: 207px;
    width: 520px;
    height: 297px;
    background: var(--card);
    overflow: hidden;
  }
  .card--back { left: 50px; }
  .card--front { left: 630px; }

  /* back side */
  .pattern-field {
    position: absolute;
    inset: 0;
    background:
      linear-gradient(135deg, rgba(79,182,232,0.55) 0%, rgba(31,95,143,0.35) 30%, rgba(23,34,51,0.6) 55%, rgba(17,24,39,0) 85%),
      var(--shade);
  }
  .back-brand {
    position: absolute;
    top: 66px;
    left: 300px;
    font-size: 13px;
    font-weight: 500;
    letter-spacing: 0.5px;
    color: var(--ink);
  }
  .services {
    position: absolute;
    left: 0; right: 0;
    bottom: 26px;
    text-align: center;
  }
  .services__title {
    font-size: 11px;
    font-weight: 500;
    letter-spacing: 0.3px;
    margin-bottom: 4px;
  }
  .services__text {
    font-size: 10.5px;
    font-weight: 400;
    color: var(--ink-soft);
  }

  /* front side */
  .name-block {
    position: absolute;
    top: 30px;
    left: 0;
    padding-left: 34px;
  }
  .name-block::before {
    content: "";
    position: absolute;
    left: 0; top: 4px;
    width: 20px; height: 50px;
    background: var(--ink);
  }
  .name {
    font-size: 27px;
    line-height: 1.05;
  }
  .name__first { font-weight: 700; }
  .name__last { font-weight: 300; }
  .credential {
    font-size: 17px;
    font-weight: 400;
    margin-top: 2px;
  }
  .front-brand {
    position: absolute;
    top: 34px;
    right: 26px;
    font-size: 15px;
    font-weight: 500;
    letter-spacing: 0.4px;
  }
  .address {
    position: absolute;
    left: 34px;
    bottom: 24px;
    font-size: 13px;
    font-weight: 400;
    line-height: 1.45;
  }
  .contacts {
    position: absolute;
    right: 20px;
    bottom: 90px;
    list-style: none;
    font-size: 12px;
    line-height: 1.55;
    text-align: right;
  }
  .contacts li {
    display: flex;
    justify-content: flex-end;
    align-items: center;
    gap: 6px;
  }
  .contacts svg { width: 11px; height: 11px; flex: none; }
</style>
</head>
<body>

  <section class="card card--back" aria-label="Card back">
    <div class="pattern-field" role="img" aria-label="Repeating company-name pattern fading from bright blue to dark navy"></div>
    <div class="back-brand">Coastal Tundrabridge Advisory</div>
    <div class="services">
      <p class="services__title">OUR SERVICES</p>
      <p class="services__text">We provide specialized permafrost services to the mining, transportation, and oil &amp; gas industries</p>
    </div>
  </section>

  <section class="card card--front" aria-label="Card front">
    <div class="name-block">
      <p class="name"><span class="name__first">Matthias</span> <span class="name__last">Korhonen</span></p>
      <p class="credential">PhD</p>
    </div>

    <div class="front-brand">Coastal Tundrabridge Advisory</div>

    <ul class="contacts">
      <li>+1-907-555-0143
        <svg viewBox="0 0 24 24" aria-hidden="true"><path fill="#fff" d="M6.6 10.8a15 15 0 0 0 6.6 6.6l2.2-2.2a1 1 0 0 1 1-.25 11.4 11.4 0 0 0 3.6.57 1 1 0 0 1 1 1V20a1 1 0 0 1-1 1A17 17 0 0 1 3 4a1 1 0 0 1 1-1h3.5a1 1 0 0 1 1 1c0 1.25.2 2.45.57 3.57a1 1 0 0 1-.25 1z"/></svg>
      </li>
      <li>mkorhonen@tundrabridgeadvisory.example
        <svg viewBox="0 0 24 24" aria-hidden="true"><rect x="2" y="5" width="20" height="14" rx="2" fill="#fff"/><path d="M3 6l9 7 9-7" fill="none" stroke="#111827" stroke-width="2"/></svg>
      </li>
      <li>www.coastaltundrabridgeadvisory.example
        <svg viewBox="0 0 24 24" aria-hidden="true"><circle cx="12" cy="12" r="10" fill="#fff"/><path d="M2 12h20M12 2c3 3 3 17 0 20M12 2c-3 3-3 17 0 20" fill="none" stroke="#111827" stroke-width="1.5"/></svg>
      </li>
    </ul>

    <address class="address" style="font-style:normal">
      PO Box 418259<br>
      Quillwater, Alaska 99642
    </address>
  </section>

</body>
</html>
```